Logo and Card design for KRV Home Solutions LLC

I need an edgier logo and business card designs. Current logo attached. I like the colors below. I would like the logo to incorporate a home in the design.
Title = Principal-Acquisitions
Email:KRVHOMESOLUTIONS@fernmail.example
555-214-0937
facebook
IG
2 sided business card with the front being contact info a slogan about selling a home fast. The back incorporating What we do. Buy houses, land, or commercial property as is. We find solutions to make the process of selling simple and fair.

Target Market(s)

Motivated house sellers.

Industry/Entity Type

Business

Contact Information for Business Card

Who we are: We are a Faith based Real Estate Investment Company. We pay cash for homes in any condition and can close quick. Whatever the reason you need to sell fast, we can help. We believe in creating win-win solutions to help you in your time of need. We care! We can help!

Logo Text

KRV Home Solutions LLC

Font styles to use
Sans Serif

Colors
33a6d7
0355a3
85abd2
cee9f5
9d9d9d
b2b2b2
ffffff

Requirements
Must have
• Old logo attached. I want something edgier.
• Company name, phone number, description on the back of what we can do. Pay all cash. Buy in as is condition. No fees,Commisions or closing costs.Close quick. No hassles with solutions to meet your unique situation.
• Call today for an offer within 24 hours.

```html
<!DOCTYPE html>
<html lang="en">
<head>
<meta charset="utf-8">
<title>KRV Home Solutions – Business Card</title>
<link rel="stylesheet" href="https://fonts.googleapis.com/css2?family=Roboto:wght@400;500;700&family=Roboto+Condensed:wght@400;500&display=swap">
<style>
  :root {
    --backdrop: #2b2b2b;
    --navy: #1f3a6e;
    --stripe: #6b6b6b;
    --back-grey: #666666;
    --white: #ffffff;
    --photo-sky: #dfe3e6;
    --photo-house: #cfcbc4;
    --photo-lawn: #b9c99a;
  }
  * { margin: 0; padding: 0; box-sizing: border-box; }
  html, body { width: 1200px; height: 960px; overflow: hidden; }
  body { background: var(--backdrop); position: relative; font-family: "Roboto", sans-serif; color: var(--white); }

  .card { position: absolute; width: 600px; height: 342px; overflow: hidden; }
  .card-front { left: 314px; top: 113px; }
  .card-back { left: 311px; top: 472px; background: var(--back-grey); }

  .front-photo {
    position: absolute; inset: 0;
    background: linear-gradient(180deg, var(--photo-sky) 0%, var(--photo-house) 45%, var(--photo-lawn) 100%);
  }
  .front-shapes { position: absolute; inset: 0; }

  .brand-name {
    position: absolute; left: 320px; top: 140px; width: 270px;
    text-align: center; color: var(--navy); white-space: nowrap;
    font-family: "Roboto", sans-serif; font-weight: 500; font-size: 19px; line-height: 24px;
  }

  .holder-name {
    position: absolute; left: 28px; top: 36px;
    font-family: "Roboto Condensed", sans-serif; font-weight: 500; font-size: 23px;
  }
  .holder-title {
    position: absolute; left: 28px; top: 64px;
    font-family: "Roboto", sans-serif; font-weight: 500; font-size: 14.5px;
  }

  .contact-list { position: absolute; left: 28px; top: 158px; list-style: none; }
  .contact-list li { display: flex; align-items: center; height: 19px; font-size: 13.5px; white-space: nowrap; }
  .contact-list svg { width: 14px; height: 14px; margin-right: 9px; fill: var(--white); flex: none; }

  .benefit-list {
    position: absolute; left: 28px; top: 226px; list-style: none;
    font-family: "Roboto Condensed", sans-serif; font-size: 14.5px; line-height: 18px;
  }
  .benefit-list li { padding-left: 13px; position: relative; }
  .benefit-list li::before { content: "•"; position: absolute; left: 0; }

  .back-brand {
    position: absolute; left: 0; right: 0; top: 102px; text-align: center;
    font-family: "Roboto", sans-serif; font-weight: 500; font-size: 21px;
  }
  .back-rule { position: absolute; left: 102px; top: 137px; width: 390px; height: 2px; background: var(--white); }

  .back-copy { position: absolute; left: 0; right: 0; text-align: center; font-size: 15px; line-height: 18px; }
  .back-copy h2 { font-size: 15px; font-weight: 500; margin-bottom: 3px; }
  .who-we-are { top: 157px; }
  .what-we-do { top: 242px; }
</style>
</head>
<body>

<section class="card card-front">
  <div class="front-photo" role="img" aria-label="Photo of a suburban house with a front lawn and a curving walkway"></div>
  <svg class="front-shapes" width="600" height="342" viewBox="0 0 600 342" aria-hidden="true">
    <polygon fill="var(--stripe)" points="311,0 318,0 281,130 460,342 451,342 269,130"/>
    <polygon fill="var(--navy)" points="0,0 311,0 269,130 451,342 0,342"/>
  </svg>

  <div class="brand-name">KRV Home Solutions LLC</div>

  <div class="holder-name">MARK ELLISON</div>
  <div class="holder-title">Principal-Acquisitions</div>

  <ul class="contact-list">
    <li><svg viewBox="0 0 24 24"><path d="M6.6 10.8a15.2 15.2 0 0 0 6.6 6.6l2.2-2.2c.3-.3.7-.4 1-.2 1.1.4 2.3.6 3.6.6.6 0 1 .4 1 1V20c0 .6-.4 1-1 1A17 17 0 0 1 3 4c0-.6.4-1 1-1h3.5c.6 0 1 .4 1 1 0 1.3.2 2.5.6 3.6.1.3 0 .7-.2 1z"/></svg>555-214-0937</li>
    <li><svg viewBox="0 0 24 24"><path d="M3 5h18v14H3z M4.5 6.5 12 12l7.5-5.5" fill="none" stroke="#fff" stroke-width="2"/></svg>KRVHOMESOLUTIONS@fernmail.example</li>
    <li><svg viewBox="0 0 24 24"><circle cx="12" cy="12" r="10"/><path d="M7 8c2 0 3 1 3 3s-2 2-2 4M14 5c0 2 2 2 3 3M15 14c1 1 1 3 0 4" stroke="var(--navy)" stroke-width="2" fill="none"/></svg>KRVHOMESOLUTIONS.example</li>
  </ul>

  <ul class="benefit-list">
    <li>Pay all cash. Buy in as is condition</li>
    <li>No fees,Commisions or closing costs</li>
    <li>Close quick. No hassles with<br>solutions to meet your unique situation</li>
    <li>Call today for an offer within 24 hours</li>
  </ul>
</section>

<section class="card card-back">
  <div class="back-brand">KRV Home Solutions LLC</div>
  <div class="back-rule"></div>

  <div class="back-copy who-we-are">
    <h2>WHO WE ARE</h2>
    <p>We are a Faith based Real Estate Investment Company. We pay cash for<br>homes in any condition and can close quick. Whatever the reason you need<br>to sell fast, we can help. We believe in creating win-win solutions to help</p>
  </div>

  <div class="back-copy what-we-do">
    <h2>WHAT WE DO</h2>
    <p>Buy houses, land, or commercial property as is.<br>We find solutions to make the process of selling simple and fair.</p>
  </div>
</section>

</body>
</html>
```